Company Website for Varnoth Signal, an open source data analytics company focused on relationship and li

I need a company/brand website for our new startup, Varnoth Signal LLC. We are a company focused on using life pattern analysis techniques, looking at relationships and how relationships, attributes, and activity cluster to infer aggregate information about individuals and groups. Our focus is on improving the digital advertising market.

We have a company logo which I will upload shortly.

Target Market(s)

Digital Advertising

Number of Pages Required

3 page

Font styles to use
Sans Serif

Requirements
Must have
• An main page, about us, contact page.
Nice to have
• Varnoth Signal relies on state of the art analytics applied to a the digital marketing space. While it is heavy in science, we also understand the art of influence. The website should have a scientific edge but also a flair that illustrates our focus on applying the hard science and analytics to influencing the behavior of people.

```html
<!DOCTYPE html>
<html lang="en">
<head>
<meta charset="utf-8">
<title>Varnoth Signal</title>
<link href="https://fonts.googleapis.com/css2?family=Open+Sans:wght@300;400;600;700;800&display=swap" rel="stylesheet">
<style>
:root{
  --orange:#f0821e;
  --blue:#1e96dc;
  --blue-deep:#1782c6;
  --ink:#333;
  --muted:#555;
  --white:#fff;
  --paper:#f7f7f7;
  --lilac:#e6e5ee;
  --dark:#242424;
  --darker:#1c1c1c;
  --grey-icon:#857b78;
}
*{box-sizing:border-box;margin:0;padding:0}
html,body{width:1200px;height:2885px;overflow:hidden}
body{font-family:'Open Sans',sans-serif;color:var(--ink);position:relative;background:var(--white)}
.abs{position:absolute}
.center{left:0;width:1200px;text-align:center}

/* header */
.site-header{position:absolute;top:0;left:0;width:1200px;height:113px;background:var(--white)}
.brand{position:absolute;left:100px;top:36px;display:flex;align-items:center;gap:10px;font-weight:700;font-size:22px;color:var(--blue)}
.brand-dot{width:14px;height:14px;border-radius:50%;background:var(--orange)}
.nav a{position:absolute;top:45px;font-size:14px;color:#222;text-decoration:none;text-transform:uppercase}
.nav a.active{color:var(--orange)}
.nav a.active::after{content:"";position:absolute;left:0;right:0;top:27px;height:2px;background:var(--orange)}

/* hero */
.hero{position:absolute;top:113px;left:0;width:1200px;height:558px;
  background:linear-gradient(120deg,#55606c 0%,#3a4550 40%,#2a3440 70%,#3c4853 100%)}
.hero-title{top:238px;font-size:108px;font-weight:800;color:var(--white);letter-spacing:2px;line-height:1}
.hero-sub{top:368px;font-size:14px;color:var(--white)}
.btn{position:absolute;background:var(--blue);color:var(--white);text-align:center;text-transform:uppercase;font-weight:600}
.hero-btn{left:508px;top:415px;width:182px;height:52px;line-height:52px;font-size:18px}
.hero-arrow{position:absolute;top:370px}

/* section titles */
.section-title{font-weight:300;font-size:40px;text-transform:uppercase;line-height:1}
.rule{position:absolute;left:550px;width:100px;height:3px;background:var(--orange)}
.rule.light{background:var(--white)}

.welcome{position:absolute;top:671px;left:0;width:1200px;height:392px;background:var(--paper)}
.body-copy{font-size:14.5px;line-height:27px;color:var(--muted)}

.services{position:absolute;top:1063px;left:0;width:1200px;height:689px;
  background:linear-gradient(135deg,#2a9fe2 0%,var(--blue) 50%,var(--blue-deep) 100%)}
.service{position:absolute;width:240px;text-align:center;color:var(--white)}
.service .ring{width:144px;height:144px;margin:0 auto;border:1.5px solid rgba(255,255,255,.85);border-radius:50%;display:flex;align-items:center;justify-content:center}
.service h3{margin-top:16px;font-size:15px;font-weight:600}

.features{position:absolute;top:1752px;left:0;width:1200px;height:588px;
  background:linear-gradient(160deg,#ecebf2 0%,var(--lilac) 60%,#dcdbe6 100%)}
.feature{position:absolute;width:280px;text-align:center}
.feature .badge{width:116px;height:116px;border-radius:50%;margin:0 auto;display:flex;align-items:center;justify-content:center}
.feature h3{margin-top:12px;font-size:22px;font-weight:600;text-transform:uppercase}
.feature p{margin-top:8px;font-size:13.5px;line-height:21px;color:var(--muted)}

.contact{position:absolute;top:2340px;left:0;width:1200px;height:473px;background:var(--dark);color:var(--white)}
.field{position:absolute;border:1px solid #5a5a5a;font-size:14px;color:#ddd;padding:0 16px;display:flex;align-items:center}
.field.area{align-items:flex-start;padding-top:12px}
.submit{left:496px;top:354px;width:208px;height:52px;line-height:52px;font-size:20px;font-weight:400}

.site-footer{position:absolute;top:2813px;left:0;width:1200px;height:72px;background:var(--darker);color:#8a8a8a;font-size:12px;text-align:center;line-height:72px}
</style>
</head>
<body>

<header class="site-header">
  <div class="brand"><span class="brand-dot"></span>Varnoth Signal</div>
  <nav class="nav">
    <a class="active" style="left:512px">Home</a>
    <a style="left:606px">About Us</a>
    <a style="left:727px">Our Services</a>
    <a style="left:869px">Our Features</a>
    <a style="left:1019px">Contact Us</a>
  </nav>
</header>

<section class="hero" role="img" aria-label="Photo of business people reviewing charts at a desk with a glass of water"></section>
<svg class="hero-arrow" style="left:34px" width="22" height="40" viewBox="0 0 22 40"><path d="M18 2 L4 20 L18 38" fill="none" stroke="#fff" stroke-width="2" opacity=".8"/></svg>
<svg class="hero-arrow" style="left:1134px" width="22" height="40" viewBox="0 0 22 40"><path d="M4 2 L18 20 L4 38" fill="none" stroke="#fff" stroke-width="2" opacity=".8"/></svg>
<h1 class="abs center hero-title">VARNOTH SIGNAL</h1>
<p class="abs center hero-sub">We are an open source data analytics company focused on relationship and lifestyle behaviors.</p>
<a class="btn hero-btn">Learn More</a>

<section class="welcome">
  <h2 class="abs center section-title" style="top:70px;color:#333">Welcome to Varnoth Signal</h2>
  <div class="rule" style="top:118px"></div>
  <p class="abs body-copy" style="left:120px;width:960px;top:144px;text-align:center">Sed ut perspiciatis unde omnis iste natus error sit voluptatem accusantium doloremque laudantium, totam rem aperiam, eaque ipsa quae ab illo inventore veritatis et quasi architecto beatae vitae dicta sunt explicabo. Nemo enim ipsam voluptatem quia voluptas sit aspernatur aut odit aut fugit, sed quia consequuntur magni dolores eos qui ratione voluptatem sequi nesciunt.</p>
  <p class="abs body-copy" style="left:120px;width:960px;top:255px;text-align:center">Neque porro quisquam est, qui dolorem ipsum quia dolor sit amet, consectetur, adipisci velit, sed quia non numquam eius modi tempora incidunt ut labore et dolore magnam aliquam quaerat voluptatem.</p>
</section>

<section class="services">
  <h2 class="abs center section-title" style="top:72px;color:var(--white)">Our Services</h2>
  <div class="rule light" style="top:116px"></div>

  <div class="service" style="left:138px;top:167px">
    <div class="ring"><svg width="70" height="60" viewBox="0 0 70 60" fill="none" stroke="#fff" stroke-width="3"><rect x="4" y="4" width="62" height="40" rx="2"/><path d="M28 44v8M42 44v8M20 54h30"/><path d="M12 34l12-12 10 8 14-14 10 6"/></svg></div>
    <h3>Voluptatem Accusantium</h3>
  </div>
  <div class="service" style="left:480px;top:167px">
    <div class="ring"><svg width="56" height="66" viewBox="0 0 56 66" fill="none" stroke="#fff" stroke-width="3"><rect x="16" y="4" width="34" height="44"/><rect x="10" y="10" width="34" height="44" fill="var(--blue)"/><rect x="4" y="18" width="34" height="44" fill="var(--blue)"/><path d="M10 30h22M10 38h22M10 46h22M10 54h16"/></svg></div>
    <h3>Doloremque Laudantium</h3>
  </div>
  <div class="service" style="left:838px;top:167px">
    <div class="ring"></div>
    <h3>Totam Rem Aperiam</h3>
  </div>

  <div class="service" style="left:138px;top:405px">
    <div class="ring"><svg width="70" height="70" viewBox="0 0 70 70" fill="#fff"><path d="M35 18 L58 28 L35 38 L12 28Z" opacity=".9"/><path d="M12 31 L33 40 V64 L12 54Z"/><path d="M37 40 L58 31 V54 L37 64Z" opacity=".85"/><path d="M44 6 L60 6 L54 20 L40 18Z"/></svg></div>
    <h3>Magnam Aliquam</h3>
  </div>
  <div class="service" style="left:480px;top:405px">
    <div class="ring"><svg width="70" height="70" viewBox="0 0 70 70" fill="none" stroke="#fff" stroke-width="3"><path d="M4 8h62"/><rect x="8" y="8" width="54" height="34"/><path d="M14 34l10-10 8 6 10-12 12 8"/><path d="M35 42v24M25 56l10-8 10 8"/></svg></div>
    <h3>Architecto Beatae</h3>
  </div>
  <div class="service" style="left:838px;top:405px">
    <div class="ring"><svg width="70" height="60" viewBox="0 0 70 60" fill="none" stroke="#fff" stroke-width="3"><rect x="20" y="6" width="46" height="30"/><path d="M26 28l8-8 6 5 8-10 12 6"/><path d="M14 24v30"/></svg></div>
    <h3>Inventore Veritatis</h3>
  </div>
</section>

<section class="features" role="group">
  <div class="abs" role="img" aria-label="Faint background photo of a person with rising bar charts" style="inset:0"></div>
  <h2 class="abs center section-title" style="top:72px;color:#333">Our Features</h2>
  <div class="rule" style="top:118px"></div>
  <p class="abs body-copy" style="left:130px;width:940px;top:145px;text-align:center;font-size:14px">At vero eos et accusamus et iusto odio dignissimos ducimus qui blanditiis praesentium voluptatum deleniti atque corrupti quos dolores et quas molestias excepturi sint occaecati cupiditate non provident.</p>

  <div class="feature" style="left:93px;top:259px">
    <div class="badge" style="background:var(--grey-icon)"><svg width="76" height="56" viewBox="0 0 76 56" fill="none" stroke="#fff" stroke-width="3"><circle cx="26" cy="32" r="9"/><circle cx="26" cy="32" r="17" stroke-dasharray="6 4"/><circle cx="56" cy="18" r="6"/><circle cx="56" cy="18" r="12" stroke-dasharray="4 3"/></svg></div>
    <h3 style="color:#7a716e">Integrate</h3>
    <p>Quis autem vel eum iure reprehenderit qui in ea voluptate velit esse quam nihil molestiae consequatur vel illum qui dolorem</p>
  </div>
  <div class="feature" style="left:460px;top:259px">
    <div class="badge" style="background:var(--orange)"><svg width="66" height="66" viewBox="0 0 66 66" fill="none" stroke="#fff" stroke-width="3.5"><circle cx="36" cy="28" r="18"/><path d="M23 41 L8 58"/><path d="M28 34v-6M34 34v-10M40 34v-8M46 34v-4" stroke-width="3"/></svg></div>
    <h3 style="color:var(--orange)">Analyze</h3>
    <p>But I must explain to you how all this mistaken idea of denouncing pleasure and praising pain was born and I will give you a complete</p>
  </div>
  <div class="feature" style="left:823px;top:259px">
    <div class="badge" style="background:var(--blue)"><svg width="66" height="60" viewBox="0 0 66 60" fill="#fff"><path d="M22 6 A14 14 0 1 0 36 20 H22Z"/><path d="M26 2 A14 14 0 0 1 40 16 H26Z" opacity=".85"/><rect x="8" y="48" width="7" height="10"/><rect x="20" y="42" width="7" height="16"/><rect x="32" y="36" width="7" height="22"/><rect x="44" y="28" width="7" height="30"/><rect x="56" y="18" width="7" height="40"/></svg></div>
    <h3 style="color:var(--blue)">Visualize</h3>
    <p>Nam libero tempore, cum soluta nobis est eligendi optio cumque nihil impedit quo minus id quod maxime placeat facere possimus</p>
  </div>
</section>

<section class="contact">
  <h2 class="abs center section-title" style="top:61px">Contact Us</h2>
  <div class="rule" style="top:106px"></div>
  <p class="abs center" style="top:120px;font-size:13px;color:#ddd">Customers to contact us with following genral enquiries</p>
  <div class="field" style="left:100px;top:172px;width:317px;height:44px">Name</div>
  <div class="field" style="left:440px;top:172px;width:318px;height:44px">Address</div>
  <div class="field" style="left:783px;top:172px;width:317px;height:44px">Email</div>
  <div class="field area" style="left:100px;top:237px;width:1000px;height:71px">Comments</div>
  <a class="btn submit">Submit Now !</a>
</section>

<footer class="site-footer">© 2018 Varnoth Signal.&nbsp; All right reserved . Term of Use</footer>

</body>
</html>
```